New Business card design to reflect rebrand

I would like a business card design with a good base colour for our new logo and also a placeholder for a profile pic of the card holder. the design needs to be editable to the point that we can easily change the picture of the person and use that design for printmerlo etc. we are looking at a metalic finish business card so will need a good base colour to bring out the finish.

Target Market(s)

prospective customers

Industry/Entity Type

Business

Contact Information for Business Card

I would like one editable design that we can change the name of the card holder and profile picture. The design need to be in a format that be send to printmerlo etc.

Our address is Fenwick Lodge, Copse Lane, Farnley Green, GU14 3TP Tel no. 01483 556172

Requirements
Must have
• place holder for a profile pic for the card holder. in AI or preferably PSD format

```html
<!DOCTYPE html>
<html lang="en">
<head>
<meta charset="utf-8">
<title>Halden Workplace – Business Card</title>
<link rel="stylesheet" href="https://fonts.googleapis.com/css2?family=PT+Serif:wght@400;700&display=swap">
<style>
  :root {
    --bg: #e9e6e1;
    --card-top: #ffffff;
    --card-bottom: #eceeef;
    --brand-blue: #4d6d90;
    --brand-orange: #e9822c;
    --text-grey: #5f6366;
    --photo-a: #c9ccce;
    --photo-b: #8e9295;
  }
  * { box-sizing: border-box; margin: 0; padding: 0; }
  html, body { width: 1200px; height: 902px; overflow: hidden; }
  body {
    background: var(--bg);
    font-family: "PT Serif", Georgia, serif;
    display: flex;
    flex-direction: column;
    align-items: center;
    justify-content: center;
    gap: 56px;
  }
  .card {
    position: relative;
    width: 630px;
    height: 360px;
    background: linear-gradient(160deg, var(--card-top), var(--card-bottom));
    box-shadow: 0 6px 18px rgba(0,0,0,0.18);
    overflow: hidden;
  }

  /* Front */
  .brand-name {
    position: absolute;
    left: 44px;
    top: 70px;
    font-size: 38px;
    font-weight: 700;
    color: var(--brand-blue);
    letter-spacing: 0.5px;
  }
  .profile-photo {
    position: absolute;
    right: 70px;
    top: 26px;
    width: 190px;
    height: 140px;
    border: 2px solid var(--brand-orange);
    padding: 5px;
    background: #fff;
  }
  .profile-photo .fill {
    width: 100%;
    height: 100%;
    background: linear-gradient(135deg, var(--photo-a), var(--photo-b));
  }
  .accent-right {
    position: absolute;
    right: 46px;
    top: 0;
    width: 3px;
    height: 190px;
    background: var(--brand-blue);
  }
  .divider {
    position: absolute;
    left: 0;
    right: 0;
    top: 186px;
  }
  .divider .line-blue { height: 3px; background: var(--brand-blue); }
  .divider .line-orange { height: 3px; background: var(--brand-orange); margin-top: 4px; width: 62%; }

  .holder {
    position: absolute;
    left: 44px;
    top: 214px;
  }
  .holder-name { font-size: 25px; color: var(--brand-orange); }
  .holder-role { font-size: 15px; color: var(--text-grey); margin-top: 2px; }
  .address {
    position: absolute;
    left: 44px;
    top: 286px;
    font-size: 14px;
    font-style: normal;
    line-height: 1.5;
    color: var(--text-grey);
  }
  .contacts {
    position: absolute;
    left: 370px;
    top: 214px;
    font-size: 14px;
    line-height: 1.8;
    color: var(--text-grey);
    list-style: none;
  }
  .contacts .label { display: inline-block; width: 22px; }

  /* Back */
  .back-mark {
    position: absolute;
    left: 0;
    right: 0;
    top: 118px;
    text-align: center;
    font-size: 84px;
    font-weight: 700;
    color: var(--brand-blue);
  }
  .back-web {
    position: absolute;
    left: 44px;
    bottom: 34px;
    font-size: 17px;
    font-weight: 700;
    color: var(--brand-blue);
  }
  .back-lines {
    position: absolute;
    right: 0;
    bottom: 44px;
    width: 300px;
  }
  .back-lines .line-orange { height: 3px; background: var(--brand-orange); }
  .back-lines .line-blue { height: 3px; background: var(--brand-blue); margin-top: 4px; }
</style>
</head>
<body>
  <section class="card card-front">
    <div class="accent-right"></div>
    <div class="brand-name">Halden</div>
    <div class="profile-photo">
      <div class="fill" role="img" aria-label="Profile photo of the card holder"></div>
    </div>
    <div class="divider">
      <div class="line-blue"></div>
      <div class="line-orange"></div>
    </div>
    <div class="holder">
      <div class="holder-name">Names surname</div>
      <div class="holder-role">Your Position</div>
    </div>
    <address class="address">
      Fenwick Lodge, Copse Lane,<br>
      Farnley Green, GU14 3TP
    </address>
    <ul class="contacts">
      <li><span class="label">T</span>: 01483 556172</li>
      <li><span class="label">M</span>: 07700 900318</li>
      <li><span class="label">E</span>: name@halden.co.uk</li>
    </ul>
  </section>

  <section class="card card-back">
    <div class="back-mark">Halden</div>
    <div class="back-web">www.halden.co.uk</div>
    <div class="back-lines">
      <div class="line-orange"></div>
      <div class="line-blue"></div>
    </div>
  </section>
</body>
</html>
```